Business card design for a dynamic IT consulting company

We need a business card design for a young firm, specialized in the Telecommunications/Consulting industry. The name of the company is Quindor and Partners Business Consulting Ltd. (Short name: Quindor and Partnes)
Quindor = solve read reverse, so we aim to be uncomplicated and solution-oriented. The small pipe in our logo is also related to the word solve. So we need a new business card design, which is simple, eye catching and something non traditional (I would probably prefer a square shaped design rather than a rectangle, but open for suggestions). Attached our logo.

Target Market(s)

Usually our customers are Tier1 Telecoms providers (Q-Netra, Palorix, etc) and their executives.

Industry/Entity Type

Business

Contact Information for Business Card

Name: Bence Tolnavari
Email: b.tolnavari@quindor.hu
Web: www.quindor.hu
Mobile: +36 30 518 2769
Title: Managing Director

Optional:
Company name: Quindor and Partners Ltd.
Address: 1087 Budapest, Tolvenka str. 28/C, Hungary

Font styles to use
Other font styles liked:
• helveticaneue_medium, Prime Regular are used now.

Colors

Designer to choose colors to be used in the design.

Requirements
Must have
• I would like to have a 2 sided design.
Nice to have
• I thought if we make the logo a bit bigger (without the company name), that could go to the back with the company name below. I though, if the pipe in the logo is somehow touchable on the business card, would be nice and unique.

```html
<!DOCTYPE html>
<html lang="en">
<head>
<meta charset="utf-8">
<title>Quindor and Partners – Business Card</title>
<link rel="stylesheet" href="https://fonts.googleapis.com/css2?family=Arimo:wght@400;700&display=swap">
<style>
  :root {
    --backdrop: #e4e4e4;
    --paper: #fbfbfb;
    --slate: #5a5a5c;
    --ink: #5b5b5d;
    --cyan: #1a97d5;
    --magenta: #b0308f;
    --white: #ffffff;
  }
  * { margin: 0; padding: 0; box-sizing: border-box; }
  html, body {
    width: 1200px; height: 960px; overflow: hidden;
    background: var(--backdrop);
    font-family: "Arimo", "Helvetica Neue", Arial, sans-serif;
  }
  .card {
    position: absolute; top: 309px;
    width: 343px; height: 344px;
    box-shadow: 0 2px 5px rgba(0,0,0,0.25);
    overflow: hidden;
  }
  .card--front { left: 235px; background: var(--paper); }
  .card--back { left: 623px; background: var(--slate); }

  .brand {
    position: absolute; left: 38px; top: 44px;
    display: flex; align-items: center; gap: 10px;
  }
  .brand__square { width: 14px; height: 14px; background: var(--cyan); }
  .brand__name { font-size: 27px; color: var(--ink); letter-spacing: -0.2px; }

  .person { position: absolute; left: 38px; top: 134px; }
  .person__name {
    font-size: 19px; font-weight: 700; color: var(--cyan);
    letter-spacing: 0.2px;
  }
  .person__title { font-size: 16px; color: var(--ink); margin-top: 2px; letter-spacing: 0.2px; }

  .address {
    position: absolute; left: 38px; top: 189px;
    font-size: 14px; line-height: 18px; color: var(--ink); font-style: normal;
  }
  .contacts { position: absolute; left: 38px; top: 255px; list-style: none; }
  .contacts li {
    display: flex; align-items: center; gap: 8px;
    font-size: 14px; line-height: 18px; color: var(--ink);
  }
  .contacts svg { width: 12px; height: 12px; fill: var(--cyan); }

  .card__rule {
    position: absolute; left: 0; right: 0; top: 315px;
    height: 3px; background: var(--cyan);
  }
  .card__band {
    position: absolute; left: 0; right: 0; top: 319px; bottom: 0;
    background: var(--slate);
  }

  .back-brand {
    position: absolute; left: 0; right: 0; top: 140px;
    display: flex; justify-content: center; align-items: center; gap: 12px;
  }
  .back-brand__square { width: 18px; height: 18px; background: var(--magenta); }
  .back-brand__name { font-size: 28px; color: var(--white); }
  .website {
    position: absolute; left: 0; right: 0; top: 293px;
    text-align: center; font-size: 13px; color: var(--white);
    letter-spacing: 0.62em;
  }
</style>
</head>
<body>
  <section class="card card--front" aria-label="Card front">
    <div class="brand">
      <span class="brand__square"></span>
      <span class="brand__name">Quindor &amp; Partners</span>
    </div>

    <div class="person">
      <div class="person__name">BENCE TOLNAVARI</div>
      <div class="person__title">MANAGING DIRECTOR</div>
    </div>

    <address class="address">
      Quindor and Partners Ltd.<br>
      1087 Budapest<br>
      Tolvenka str. 28/C, Hungary
    </address>

    <ul class="contacts">
      <li>
        <svg viewBox="0 0 12 12" aria-hidden="true"><path d="M3 0h6a1 1 0 0 1 1 1v10a1 1 0 0 1-1 1H3a1 1 0 0 1-1-1V1a1 1 0 0 1 1-1zm0 1.5v8h6v-8z"/></svg>
        +36 30 518 2769
      </li>
      <li>
        <svg viewBox="0 0 12 12" aria-hidden="true"><path d="M0 3h12v7H0z M0 3l6 4 6-4" /></svg>
        b.tolnavari@quindor.hu
      </li>
    </ul>

    <div class="card__rule"></div>
    <div class="card__band"></div>
  </section>

  <section class="card card--back" aria-label="Card back">
    <div class="back-brand">
      <span class="back-brand__square"></span>
      <span class="back-brand__name">Quindor</span>
    </div>
    <div class="website">www.quindor.hu</div>
  </section>
</body>
</html>
```